Basic / Quick Business Card

Quick easy design project!

Need a one sided basic business card that matches font & style of brand and bottle label for our gourmet condiment, Brindle Harrow Sauce. Brindle Harrow Sauce is sold in specialty retail, gourmet groceries and appears on chef-driven restaurant menus, so the target market is a high end, gourmet, artisan-made food-loving customer.

Files Included:
Sauce Bottle Label
Brindle Harrow Sauce Round Logos

**About the logos - the logo may be used in a circle or alone vertically as on side of the bottle label**

Layout of Card:
May be vertical or horizontal based on designer ideas.

Logo usage (in circle vs. stand alone vertical logo) is up to designers descretion as well.

Reverse side of business card will be various high end / professional product photos / food shots using us.kelbo.com system. **Designer on this project will NOT design a reserve for the card.**

Paper that will be used for printing:
Kelbo Standard - it's a WHITE paper, but we use a cream background on Brindle Harrow Sauce branding, so please take this into account on design to stay brand consistent.

Elements & Copy for Card:
1. Logo in either script horizontal or vertical version
2. Copy: "Artisan Made - Small Batch"
3. Name - Wes Dorrance
4. Title - Creator
5. Phone - xxx.xxx.xxxx
6. xxxx@brindleharrow.com
7. URL: brindleharrowsauce.com
8. Social Media: @getbrindleharrow on Quillo / Pagora / Lumigrid

Please provide final files in Illustrator or InDesign format.

```html
<!DOCTYPE html>
<html lang="en">
<head>
<meta charset="utf-8">
<title>Brindle Harrow Sauce – Business Card</title>
<link href="https://fonts.googleapis.com/css2?family=Cambo&display=swap" rel="stylesheet">
<style>
  :root {
    --backdrop: #d9d4cc;
    --card-dark: #2a2627;
    --cream: #eeecd9;
    --gold: #eeb214;
    --ink: #2b2624;
    --white: #ffffff;
  }
  * { box-sizing: border-box; margin: 0; padding: 0; }
  html, body {
    width: 1200px; height: 804px; overflow: hidden;
    background: var(--backdrop);
    font-family: "Cambo", Georgia, serif;
  }
  .card {
    position: absolute; left: 100px; top: 116px;
    width: 1000px; height: 572px;
    background: var(--card-dark);
    overflow: hidden;
    box-shadow: 0 10px 30px rgba(0,0,0,.25);
  }
  .brand-mark {
    position: absolute; left: 130px; top: 80px;
    width: 300px; height: 300px;
  }
  .brand-name {
    position: absolute; left: 0; top: 0; width: 300px; height: 300px;
    display: flex; flex-direction: column; justify-content: center; align-items: center;
    color: var(--gold); font-size: 44px; line-height: 1.05; text-align: center;
  }
  .brand-name .small { font-size: 26px; letter-spacing: 2px; margin-top: 6px; }
  .name-tag {
    position: absolute; left: 160px; bottom: 0;
    width: 270px; height: 118px;
  }
  .name-tag svg { position: absolute; inset: 0; }
  .name-tag .text {
    position: absolute; left: 0; right: 0; top: 38px;
    text-align: center; color: var(--white);
    font-size: 30px; line-height: 1.05;
  }
  .info-panel {
    position: absolute; left: 505px; top: 42px;
    width: 455px; height: 488px;
    background: var(--cream);
    padding: 40px 30px 0 30px;
    color: var(--ink);
  }
  .contact-list { list-style: none; font-size: 23px; line-height: 1.45; }
  .contact-list li { display: flex; align-items: center; gap: 10px; }
  .contact-list svg { width: 18px; height: 18px; flex: none; }
  .dotted-rule {
    border: none; border-top: 4px dotted var(--gold);
    margin: 20px 0;
  }
  .social { font-size: 22px; display: flex; align-items: center; gap: 14px; }
  .social .networks { font-size: 17px; color: #3b5f8f; }
  .tagline { font-size: 26px; margin-top: 14px; }
  .promise-band {
    position: absolute; left: 12px; right: 12px; bottom: 12px;
    height: 70px; background: var(--gold);
    color: var(--white); font-size: 24px;
    display: flex; align-items: center; padding-left: 18px;
  }
</style>
</head>
<body>
  <div class="card">
    <div class="brand-mark">
      <svg width="300" height="300" viewBox="0 0 300 300" aria-hidden="true">
        <circle cx="150" cy="150" r="144" fill="none" stroke="var(--gold)" stroke-width="8"/>
      </svg>
      <div class="brand-name">Brindle<br>Harrow<span class="small">Sauce</span></div>
    </div>

    <div class="name-tag">
      <svg width="270" height="118" viewBox="0 0 270 118" aria-hidden="true">
        <polygon points="0,40 135,0 270,40 270,118 0,118" fill="var(--white)"/>
        <polygon points="10,46 135,10 260,46 260,118 10,118" fill="var(--gold)"/>
      </svg>
      <div class="text">Wes Dorrance<br>Creator</div>
    </div>

    <div class="info-panel">
      <ul class="contact-list">
        <li>
          <svg viewBox="0 0 20 20" aria-hidden="true"><circle cx="10" cy="10" r="9" fill="none" stroke="var(--ink)" stroke-width="2"/><path d="M7 5 l2 0 l1 3 l-1.5 1 q1 2 3 3 l1 -1.5 l3 1 l0 2 q-6 1 -8.5 -8.5z" fill="var(--ink)"/></svg>
          555-014-2290
        </li>
        <li>
          <svg viewBox="0 0 20 20" aria-hidden="true"><rect x="1" y="4" width="18" height="12" rx="1" fill="var(--ink)"/><path d="M1 5 l9 6 l9 -6" fill="none" stroke="var(--cream)" stroke-width="1.5"/></svg>
          wdorrance@brindleharrow.com
        </li>
        <li>
          <svg viewBox="0 0 20 20" aria-hidden="true"><circle cx="10" cy="10" r="8.5" fill="none" stroke="var(--ink)" stroke-width="2"/><ellipse cx="10" cy="10" rx="3.5" ry="8.5" fill="none" stroke="var(--ink)" stroke-width="1.5"/><path d="M2 10 h16 M3.5 6 h13 M3.5 14 h13" stroke="var(--ink)" stroke-width="1.3"/></svg>
          www.brindleharrowsauce.com
        </li>
      </ul>
      <hr class="dotted-rule">
      <div class="social">Follow Us On <span class="networks">Pagora · Quillo · Lumigrid</span></div>
      <hr class="dotted-rule">
      <p class="tagline">sweet &amp; spicy</p>
      <div class="promise-band">Artisan Made - Small Batch</div>
    </div>
  </div>
</body>
</html>
```